Small Catering Menu

I am looking to make a small menu for catering for my company. I am thinking of a small A5 size booklet which will also have some pictures and the cover needs to be attractive.
Likely to be 8-12 pages depending upon your design (could be less or more). I need 2-3 pages as proposal concept (Cover, inside first page and one menu page) and if we like it we will make the project guaranteed before finishing the rest of the project to add security for the designer.
Pictures will be provided to the designer whose concept is the best as they are too heavy. But use generic photos for now (rather large ones) if possible.
Logo is available and so is the inside text as well as some other tidbits.
I will provide the fonts too to ensure it maintains the corporate integrity that we are following.
Industry/Entity Type
Catering

```html
<!DOCTYPE html>
<html lang="en">
<head>
<meta charset="utf-8">
<title>Catering Menu – Menu Page</title>
<link rel="stylesheet" href="https://fonts.googleapis.com/css2?family=Open+Sans:wght@300;400;600&family=Tinos&display=swap">
<style>
  :root {
    --backdrop: #e4e2df;
    --paper: #f4f4f3;
    --ink: #3a3a3a;
    --ink-soft: #555555;
    --rule: #c9c9c9;
    --price-red: #d0202a;
    --band: #050505;
    --band-text: #f2f2f2;
    --photo-warm-a: #5a3418;
    --photo-warm-b: #a8713a;
    --photo-dark-a: #1c1a18;
    --photo-dark-b: #6b5a3e;
    --photo-green-a: #183a2c;
    --photo-green-b: #6f9a4a;
    --photo-rose-a: #7a5038;
    --photo-rose-b: #c99a72;
  }
  * { box-sizing: border-box; margin: 0; padding: 0; }
  html, body {
    width: 1200px; height: 1000px; overflow: hidden;
    background: var(--backdrop);
  }
  .menu-page {
    position: absolute; left: 280px; top: 48px;
    width: 640px; height: 904px;
    background: var(--paper);
    box-shadow: 0 6px 22px rgba(0,0,0,.18);
    font-family: "Open Sans", sans-serif;
    color: var(--ink);
    overflow: hidden;
  }
  .featured-row {
    display: flex; gap: 20px; padding: 36px 26px 0;
  }
  .featured-item { width: 183px; }
  .photo { display: block; width: 100%; }
  .featured-item .photo { height: 118px; }
  .photo-coffee { background: radial-gradient(ellipse at 45% 60%, var(--photo-warm-b), var(--photo-warm-a)); }
  .photo-cheese { background: radial-gradient(ellipse at 50% 60%, #c9a24a, var(--photo-dark-a) 75%); }
  .photo-cake { background: radial-gradient(ellipse at 50% 55%, #9a6a3c, #3a2414 80%); }
  .item-head {
    display: flex; align-items: baseline; gap: 4px; margin-top: 8px;
  }
  .item-name { font-size: 12.5px; font-weight: 600; color: var(--ink); white-space: nowrap; }
  .item-leader { flex: 1; border-bottom: 1px dotted var(--rule); transform: translateY(-3px); }
  .item-price { font-size: 12px; color: var(--price-red); font-weight: 600; }
  .item-price sup { font-size: 7px; }
  .item-desc { font-size: 9.5px; color: var(--ink-soft); line-height: 1.3; margin-top: 3px; }

  .section-title {
    display: flex; align-items: center; gap: 18px;
    margin: 34px 26px 0;
    font-family: "Tinos", serif; font-size: 26px; color: #222;
    white-space: nowrap;
  }
  .section-title::before, .section-title::after {
    content: ""; flex: 1; border-top: 1px solid var(--rule);
  }
  .dish-list { list-style: none; margin: 36px 30px 0 30px; }
  .dish {
    display: flex; align-items: flex-end; gap: 10px; margin-bottom: 34px;
  }
  .dish-number { font-size: 30px; font-weight: 300; color: #555; line-height: 1; }
  .dish-text { display: flex; flex-direction: column; }
  .dish-name { font-size: 14px; color: #555; }
  .dish-desc { font-size: 10px; color: var(--ink-soft); }
  .dish-leader { flex: 1; border-bottom: 1px dotted #999; margin: 0 14px 6px 30px; }
  .dish-price { font-size: 12px; color: #555; margin-bottom: 2px; }

  .highlight-band {
    position: absolute; left: 0; right: 0; bottom: 0; height: 372px;
    background: var(--band);
    display: flex; gap: 18px; padding: 26px 22px 0;
  }
  .highlight-item { width: 186px; text-align: center; }
  .highlight-item .photo { height: 232px; }
  .photo-smoothie { background: linear-gradient(160deg, var(--photo-green-a), #2f5a3a 55%, var(--photo-green-b)); }
  .photo-salami { background: radial-gradient(ellipse at 50% 55%, #b0806a, var(--photo-dark-a) 80%); }
  .photo-berries { background: radial-gradient(ellipse at 50% 50%, var(--photo-rose-b), var(--photo-rose-a) 85%); }
  .highlight-name {
    margin-top: 14px; font-size: 14px; font-weight: 600; color: var(--band-text); line-height: 1.3;
  }
  .highlight-desc { font-size: 10.5px; font-weight: 600; color: var(--band-text); margin-top: 2px; }
  .highlight-price { font-size: 15px; font-weight: 600; color: var(--price-red); margin-top: 8px; }
</style>
</head>
<body>
<main class="menu-page">
  <section class="featured-row">
    <article class="featured-item">
      <span class="photo photo-coffee" role="img" aria-label="Photo of coffee cups, a grinder and croissants"></span>
      <div class="item-head"><span class="item-name">Dynamite Shrimps</span><span class="item-leader"></span><span class="item-price"><sup>$</sup>4.50</span></div>
      <p class="item-desc">The standard of Lorem Ipsum used since 1500s is reproduced below.</p>
    </article>
    <article class="featured-item">
      <span class="photo photo-cheese" role="img" aria-label="Photo of a cheese board with cherry tomatoes"></span>
      <div class="item-head"><span class="item-name">Dynamite Shrimps</span><span class="item-leader"></span><span class="item-price"><sup>$</sup>4.50</span></div>
      <p class="item-desc">The standard of Lorem Ipsum used since 1500s is reproduced below.</p>
    </article>
    <article class="featured-item">
      <span class="photo photo-cake" role="img" aria-label="Photo of bundt cakes on a wooden board"></span>
      <div class="item-head"><span class="item-name">Dynamite Shrimps</span><span class="item-leader"></span><span class="item-price"><sup>$</sup>4.50</span></div>
      <p class="item-desc">The standard of Lorem Ipsum used since 1500s is reproduced below.</p>
    </article>
  </section>

  <h2 class="section-title">Recommended Dishes</h2>

  <ol class="dish-list">
    <li class="dish">
      <span class="dish-number">01</span>
      <span class="dish-text"><span class="dish-name">Dynamite Shrimps</span><span class="dish-desc">your food item description, ingredients etc..</span></span>
      <span class="dish-leader"></span>
      <span class="dish-price">$4,5</span>
    </li>
    <li class="dish">
      <span class="dish-number">02</span>
      <span class="dish-text"><span class="dish-name">Tuna Fish Cutlets.</span><span class="dish-desc">your food item description, ingredients etc.. goes here</span></span>
      <span class="dish-leader"></span>
      <span class="dish-price">$4,5</span>
    </li>
  </ol>

  <section class="highlight-band">
    <article class="highlight-item">
      <span class="photo photo-smoothie" role="img" aria-label="Photo of a green kiwi smoothie with sliced kiwi"></span>
      <h3 class="highlight-name">Pan Fried Baja Fish Fillet in Ciabatta Bread whith Cheese</h3>
      <p class="highlight-desc">your food item description...</p>
      <p class="highlight-price">$6.99</p>
    </article>
    <article class="highlight-item">
      <span class="photo photo-salami" role="img" aria-label="Photo of cured sausages and cheese"></span>
      <h3 class="highlight-name">Pan Fried Baja Fish Fillet in Ciabatta Bread whith Cheese</h3>
      <p class="highlight-desc">your food item description...</p>
      <p class="highlight-price">$6.99</p>
    </article>
    <article class="highlight-item">
      <span class="photo photo-berries" role="img" aria-label="Photo of strawberries with chocolate sauce in a bowl"></span>
      <h3 class="highlight-name">Pan Fried Baja Fish Fillet in Ciabatta Bread whith Cheese</h3>
      <p class="highlight-desc">your food item description...</p>
      <p class="highlight-price">$6.99</p>
    </article>
  </section>
</main>
</body>
</html>
```